Modern Business Card for Larkwell 2018

Our company assumes the best about people. We are creating an online community of entrepreneurs and business leaders who struggle with marketing their business online.

This business card should POP! We recently got a new logo and are launching a new website next month, so our business cards should make a statement that feels:
-Fresh
-Smart
-Trustworthy
-Fun

Target Market(s)

small business owners, entrepreneurs

Industry/Entity Type

Digital Marketing

Contact Information for Business Card

Dimensions: 3.5" x 2"

Font styles to use
Sans Serif

Colors
f37122
ffffff

Requirements
Must have
• We need a business card with a modern, bold design. We will use one side of the card as a lead-generation offer, so text on one side will need to fit up to 140 characters. The business card should stick to our core colors (orange, black, and white).
Nice to have
• We think a vertical "portrait" design could be interesting.
Should not have
• Should not look like a traditional business card. The round icon should stand out from a distance.

```html
<!DOCTYPE html>
<html lang="en">
<head>
<meta charset="utf-8">
<title>Larkwell Business Card</title>
<link rel="stylesheet" href="https://fonts.googleapis.com/css2?family=Kaushan+Script&family=Montserrat:wght@700&family=Permanent+Marker&family=Roboto:wght@400;500;700&family=Roboto+Condensed:wght@700&display=swap">
<style>
  :root {
    --brand-orange: #f26a27;
    --card-white: #f7f7f7;
    --ink: #111111;
    --page-bg: #e8e5e1;
    --rule: #333333;
    --white: #ffffff;
  }
  * { margin: 0; padding: 0; box-sizing: border-box; }
  html, body {
    width: 1200px; height: 960px; overflow: hidden;
    background: var(--page-bg);
    font-family: "Roboto", Arial, sans-serif;
  }
  .canvas { position: relative; width: 1200px; height: 960px; }

  .card {
    position: absolute;
    background: var(--card-white);
    border-radius: 22px;
    overflow: hidden;
    box-shadow: 0 2px 6px rgba(0,0,0,0.15);
  }

  /* Front */
  .card-front { left: 314px; top: 113px; width: 600px; height: 343px; text-align: center; }
  .front-mark {
    position: absolute; left: 252px; top: 62px;
    width: 96px; height: 96px; border-radius: 50%;
    background: var(--brand-orange);
  }
  .front-brand {
    position: absolute; left: 0; right: 0; top: 166px;
    font-family: "Montserrat", Arial, sans-serif; font-weight: 700;
    font-size: 22px; line-height: 1; letter-spacing: 1px; color: var(--brand-orange);
  }
  .holder-name {
    position: absolute; left: 0; right: 0; top: 222px;
    font-family: "Kaushan Script", cursive;
    font-size: 38px; font-weight: 400; line-height: 1; color: var(--ink);
    text-transform: uppercase;
  }
  .holder-title {
    position: absolute; left: 0; right: 0; top: 265px;
    font-size: 15px; font-weight: 400; letter-spacing: 0.3px; line-height: 18px; color: var(--ink);
  }
  .holder-email {
    position: absolute; left: 0; right: 0; top: 285px;
    font-size: 14px; line-height: 18px; color: var(--ink);
  }

  /* Back */
  .card-back { left: 312px; top: 472px; width: 598px; height: 342px; }
  .offer-band {
    position: absolute; left: 0; top: 0; width: 100%; height: 218px;
    background: var(--brand-orange); color: var(--white);
  }
  .brand-lockup { position: absolute; left: 20px; width: 278px; top: 58px; text-align: center; }
  .brand-mark {
    display: block; margin: 0 auto 16px;
    width: 36px; height: 36px; border-radius: 50%;
    background: var(--white);
  }
  .brand-name {
    font-family: "Montserrat", Arial, sans-serif; font-weight: 700;
    font-size: 34px; line-height: 1; letter-spacing: 1px;
  }
  .brand-tagline {
    margin-top: 8px;
    font-family: "Permanent Marker", sans-serif;
    font-size: 11.5px; line-height: 14px; letter-spacing: 0.6px; text-transform: uppercase;
  }
  .band-divider {
    position: absolute; left: 296px; top: 28px; width: 1px; height: 166px;
    background: rgba(255,255,255,0.6);
  }
  .offer-copy { position: absolute; left: 322px; top: 29px; width: 262px; }
  .offer-headline {
    font-family: "Roboto", Arial, sans-serif; font-weight: 700;
    font-size: 18.5px; line-height: 21px; text-transform: uppercase;
  }
  .offer-body { margin-top: 5px; width: 200px; font-size: 15px; line-height: 19px; }
  .offer-link { margin-top: 8px; font-size: 19px; font-weight: 700; line-height: 22px; }

  .note-line {
    position: absolute; left: 35px; width: 520px; height: 1px;
    background: var(--rule);
  }
  .note-line-1 { top: 260px; }
  .note-line-2 { top: 300px; }
</style>
</head>
<body>
<main class="canvas">
  <section class="card card-front" aria-label="Card front">
    <span class="front-mark" aria-hidden="true"></span>
    <div class="front-brand">LARKWELL</div>
    <h1 class="holder-name">Dana Whitfield</h1>
    <p class="holder-title">STORY MARKETING COACH</p>
    <p class="holder-email">dana@larkwellnow.com</p>
  </section>

  <section class="card card-back" aria-label="Card back">
    <div class="offer-band">
      <div class="brand-lockup">
        <span class="brand-mark" aria-hidden="true"></span>
        <div class="brand-name">LARKWELL</div>
        <div class="brand-tagline">Share ideas that move people</div>
      </div>
      <div class="band-divider"></div>
      <div class="offer-copy">
        <p class="offer-headline">Grow a loyal audience.<br>Win more clients.<br>Build a lasting brand.</p>
        <p class="offer-body">Get your free Larkwell Starter Package and our marketing guide today at</p>
        <p class="offer-link">Larkwellnow.com/start</p>
      </div>
    </div>
    <div class="note-line note-line-1"></div>
    <div class="note-line note-line-2"></div>
  </section>
</main>
</body>
</html>
```